Looking for a cool & simple business-card-design for digital agency

Hi!

We are a web agency that offers Reputation Management, Vextor & Seo Services and software development. We like cool things, we like innovative styles.

We have uploaded our logo.

Project Deadline Extended Reason: Client does not want any designs with the colorful logo. Please send us submissions ONLY with the blac and white logo. What the client would like to see:1) Back of the card: is a silver logo on a black background2) front of the card with all the data, please use white background and black logo thank you Added Friday, May 8, 2015

Industry/Entity Type

Software

```html
<!DOCTYPE html>
<html lang="en">
<head>
<meta charset="utf-8">
<title>Lumenfeld AG – Business Card</title>
<link rel="stylesheet" href="https://fonts.googleapis.com/css2?family=Lato:wght@400;700;900&display=swap">
<style>
  :root {
    --page-bg: #d9d6d2;
    --card-light: #f3f2f0;
    --card-mid: #e4e3e1;
    --ink: #2b2b2b;
    --ink-soft: #3a3a3a;
    --band-dark: #050505;
    --band-fade: #2e2e2e;
    --band-text: #d8d4d0;
    --band-link: #cbb5b8;
    --icon: #bfb8b0;
    --mark: #1c1c1c;
  }
  * { box-sizing: border-box; margin: 0; padding: 0; }
  html, body {
    width: 1200px; height: 969px; overflow: hidden;
    background: var(--page-bg);
    font-family: "Lato", Arial, sans-serif;
  }
  .card {
    position: absolute; left: 100px; top: 207px;
    width: 1000px; height: 555px;
    background: linear-gradient(120deg, var(--card-light), var(--card-mid) 60%, var(--card-light));
    border: 1px solid #ffffff;
    box-shadow: 0 6px 24px rgba(0,0,0,0.18);
    overflow: hidden;
  }
  .brand {
    position: absolute; left: 73px; top: 64px;
    display: flex; align-items: center; gap: 48px;
  }
  .brand-mark { width: 78px; height: 78px; background: var(--ink); }
  .brand-text { border-left: 2px solid var(--ink); padding-left: 14px; }
  .brand-name {
    font-weight: 900; font-size: 50px; line-height: 1; color: var(--ink);
    letter-spacing: 6px;
  }
  .brand-tagline {
    font-weight: 400; font-size: 27px; line-height: 1.2; color: var(--ink);
    letter-spacing: 9.5px; margin-top: 4px;
  }
  .person { position: absolute; left: 73px; top: 220px; color: var(--ink); }
  .person-name { font-weight: 700; font-size: 31px; }
  .person-role { font-weight: 400; font-size: 27px; color: var(--ink-soft); margin-top: 2px; }
  .contact-band {
    position: absolute; left: 0; top: 334px; width: 76%; height: 188px;
    background: linear-gradient(90deg, var(--band-dark) 0%, var(--band-dark) 55%, var(--band-fade) 80%, var(--band-dark) 100%);
  }
  .contact-list { position: absolute; left: 56px; top: 24px; list-style: none; }
  .contact-list li {
    display: flex; align-items: center; gap: 10px;
    font-size: 26px; line-height: 35px; color: var(--band-text);
  }
  .contact-list li.link { color: var(--band-link); }
  .contact-list svg { width: 24px; height: 24px; fill: none; stroke: var(--icon); stroke-width: 2; }
  .band-mark {
    position: absolute; right: 6px; top: 336px;
    width: 186px; height: 186px; background: var(--mark);
  }
</style>
</head>
<body>
  <div class="card">
    <div class="brand">
      <div class="brand-mark"></div>
      <div class="brand-text">
        <div class="brand-name">Lumenfeld AG</div>
        <div class="brand-tagline">DIGITALE STRATEGIEN</div>
      </div>
    </div>

    <div class="person">
      <div class="person-name">Mara Keller</div>
      <div class="person-role">Director</div>
    </div>

    <div class="contact-band">
      <ul class="contact-list">
        <li>
          <svg viewBox="0 0 24 24"><path d="M4 9c0-3 3-4 8-4s8 1 8 4l-3 1-1-2H8l-1 2zM6 12h12l1 7H5z"/></svg>
          041 276 3850
        </li>
        <li>
          <svg viewBox="0 0 24 24"><rect x="7" y="3" width="10" height="18" rx="2"/><line x1="11" y1="18" x2="13" y2="18"/></svg>
          079 5128 403
        </li>
        <li class="link">
          <svg viewBox="0 0 24 24"><rect x="3" y="6" width="18" height="12"/><path d="M3 6l9 7 9-7"/></svg>
          info@lumenfeldag.com
        </li>
        <li class="link">
          <svg viewBox="0 0 24 24"><circle cx="12" cy="12" r="9"/><ellipse cx="12" cy="12" rx="4" ry="9"/><line x1="3" y1="12" x2="21" y2="12"/></svg>
          www.lumenfeldag.com
        </li>
      </ul>
    </div>
    <div class="band-mark"></div>
  </div>
</body>
</html>
```